Business Card Design

We are a commercial real estate brokerage in San Francisco, leasing office buildings downtown.
I would like a clean, elegant look. Simple but powerful .

Industry/Entity Type

Business

Contact Information for Business Card

Derek Holloway
lic# 07258143
415.555.0172
derek@velt-commercial.example
velt-commercial.example

```html
<!DOCTYPE html>
<html lang="en">
<head>
<meta charset="utf-8">
<title>Velt Commercial — Business Card</title>
<link href="https://fonts.googleapis.com/css2?family=Roboto:wght@400;500;700&display=swap" rel="stylesheet">
<style>
  :root {
    --backdrop: #e2e2e2;
    --card-white: #f4f4f3;
    --navy: #1f2d40;
    --band-blue: #3f7fbf;
    --band-light: #6c9fd3;
    --name-blue: #3b6fb6;
    --ink: #3a3f48;
    --logo-slate: #4d5b78;
    --icon-blue: #4a7cc0;
    --contact-text: #e9eef5;
  }
  * { box-sizing: border-box; margin: 0; padding: 0; }
  html, body {
    width: 1200px; height: 900px; overflow: hidden;
    background: var(--backdrop);
    font-family: "Roboto", Arial, sans-serif;
  }
  .business-card {
    position: absolute; left: 75px; top: 150px;
    width: 1050px; height: 600px;
    background: var(--card-white);
    box-shadow: 0 6px 18px rgba(0,0,0,0.18);
    overflow: hidden;
  }
  .card-shapes { position: absolute; inset: 0; }
  .name-plate {
    position: absolute; left: 0; top: 50px;
    width: 450px; height: 110px;
    background: var(--card-white);
    box-shadow: 0 3px 8px rgba(0,0,0,0.35);
    padding: 22px 0 0 60px;
  }
  .agent-name {
    color: var(--name-blue); font-size: 34px; font-weight: 400;
    letter-spacing: 1px; text-transform: uppercase; line-height: 1;
  }
  .agent-license {
    color: var(--ink); font-size: 20px; margin-top: 6px; letter-spacing: 0.5px;
  }
  .contact-list { position: absolute; left: 60px; top: 235px; list-style: none; }
  .contact-item {
    display: flex; align-items: center; gap: 22px;
    height: 40px; margin-bottom: 30px;
    color: var(--contact-text); font-size: 20px; letter-spacing: 0.3px;
    white-space: nowrap;
  }
  .contact-icon {
    width: 40px; height: 40px; background: var(--icon-blue);
    display: flex; align-items: center; justify-content: center; flex: none;
  }
  .brand-lockup {
    position: absolute; left: 640px; top: 245px;
    display: flex; align-items: center; gap: 22px;
  }
  .brand-square { width: 18px; height: 18px; background: var(--logo-slate); }
  .brand-name {
    color: var(--logo-slate); font-weight: 700; line-height: 0.95;
    text-transform: uppercase;
  }
  .brand-name .brand-primary { display: block; font-size: 78px; letter-spacing: 3px; }
  .brand-name .brand-secondary { display: block; font-size: 30px; letter-spacing: 2px; }
</style>
</head>
<body>
  <article class="business-card">
    <svg class="card-shapes" width="1050" height="600" viewBox="0 0 1050 600" aria-hidden="true">
      <polygon points="0,0 560,0 470,225 470,600 0,600" fill="var(--navy)"/>
      <polygon points="560,0 625,0 520,250 520,600 470,600 470,225" fill="var(--band-blue)"/>
      <polygon points="470,225 485,210 485,600 470,600" fill="var(--band-light)"/>
      <line x1="505" y1="160" x2="548" y2="70" stroke="var(--band-light)" stroke-width="3"/>
      <line x1="455" y1="330" x2="455" y2="560" stroke="var(--band-light)" stroke-width="2" opacity="0.6"/>
    </svg>

    <header class="name-plate">
      <h1 class="agent-name">Derek Holloway</h1>
      <p class="agent-license">LIC# 07258143</p>
    </header>

    <ul class="contact-list">
      <li class="contact-item">
        <span class="contact-icon">
          <svg width="22" height="22" viewBox="0 0 24 24" aria-hidden="true"><path fill="#fff" d="M6.6 10.8a15.1 15.1 0 0 0 6.6 6.6l2.2-2.2a1 1 0 0 1 1-.25 11.4 11.4 0 0 0 3.6.57 1 1 0 0 1 1 1V20a1 1 0 0 1-1 1A17 17 0 0 1 3 4a1 1 0 0 1 1-1h3.5a1 1 0 0 1 1 1c0 1.25.2 2.45.57 3.6a1 1 0 0 1-.25 1z"/></svg>
        </span>
        <span>415.555.0172</span>
      </li>
      <li class="contact-item">
        <span class="contact-icon">
          <svg width="22" height="22" viewBox="0 0 24 24" aria-hidden="true"><rect x="3" y="5" width="18" height="14" fill="none" stroke="#fff" stroke-width="2"/><path d="M3 6l9 7 9-7" fill="none" stroke="#fff" stroke-width="2"/></svg>
        </span>
        <span>derek@velt-commercial.example</span>
      </li>
      <li class="contact-item">
        <span class="contact-icon">
          <svg width="22" height="22" viewBox="0 0 24 24" aria-hidden="true"><circle cx="12" cy="12" r="9" fill="none" stroke="#fff" stroke-width="2"/><path d="M3 12h18M12 3c3 3 3 15 0 18M12 3c-3 3-3 15 0 18" fill="none" stroke="#fff" stroke-width="1.6"/></svg>
        </span>
        <span>velt-commercial.example</span>
      </li>
    </ul>

    <div class="brand-lockup">
      <span class="brand-square" aria-hidden="true"></span>
      <p class="brand-name">
        <span class="brand-primary">Velt</span>
        <span class="brand-secondary">Commercial</span>
      </p>
    </div>
  </article>
</body>
</html>
```